Step and Repeat Backdrop for wedding reception photo booth

Would like to have a Step and Repeat Backdrop (8 foot high by 10 foot wide) that incorporates the wedding logo (attached) and the names Helen and Gavin. Background should be white, and wedding colors are burgundy and gold. Show me creativity :-) I have included some random samples.

```html
<!DOCTYPE html>
<html lang="en">
<head>
<meta charset="utf-8">
<title>Helen &amp; Gavin – Step and Repeat Backdrop</title>
<link rel="stylesheet" href="https://fonts.googleapis.com/css2?family=Playfair+Display:wght@500&display=swap">
<style>
  :root {
    --burgundy: #7d0022;
    --gold: #8b7512;
    --white: #ffffff;
    --page: #ececef;
    --flourish-on-dark: rgba(255, 255, 255, 0.28);
    --flourish-burgundy: rgba(125, 0, 34, 0.35);
    --flourish-gold: rgba(139, 117, 18, 0.35);
    --tile: 94px;
    --gap-x: 20px;
    --gap-y: 14px;
  }
  * { box-sizing: border-box; margin: 0; padding: 0; }
  html, body { width: 1200px; height: 1200px; overflow: hidden; }
  body {
    background: var(--page);
    display: flex;
    align-items: center;
    justify-content: center;
    font-family: "Playfair Display", Georgia, serif;
  }
  .backdrop {
    width: 1160px;
    height: 962px;
    background: var(--white);
    padding: 16px 20px;
    display: flex;
    flex-direction: column;
    gap: 14px;
  }
  .flourish-row {
    display: grid;
    grid-template-columns: repeat(10, var(--tile));
    column-gap: var(--gap-x);
    height: 26px;
  }
  .flourish {
    align-self: center;
    height: 12px;
    border-radius: 6px;
  }
  .flourish--gold { background: var(--flourish-gold); }
  .flourish--burgundy { background: var(--flourish-burgundy); }

  .tile-grid {
    display: grid;
    grid-template-columns: repeat(10, var(--tile));
    grid-template-rows: repeat(8, var(--tile));
    column-gap: var(--gap-x);
    row-gap: var(--gap-y);
  }
  .tile {
    display: flex;
    flex-direction: column;
    align-items: center;
    justify-content: center;
    gap: 5px;
    color: var(--white);
  }
  .tile--burgundy { background: var(--burgundy); }
  .tile--gold { background: var(--gold); }
  .tile__flourish {
    width: 62px;
    height: 10px;
    border-radius: 5px;
    background: var(--flourish-on-dark);
  }
  .tile__monogram {
    font-size: 29px;
    font-weight: 500;
    line-height: 1;
    letter-spacing: -1px;
  }
  .feature {
    grid-column: 4 / 8;
    grid-row: 4 / 7;
    background: var(--gold);
    color: var(--white);
    display: flex;
    flex-direction: column;
    align-items: center;
    justify-content: center;
    gap: 18px;
  }
  .feature__flourish {
    width: 290px;
    height: 60px;
    border-radius: 30px;
    background: var(--flourish-on-dark);
  }
  .feature__monogram {
    font-size: 112px;
    font-weight: 500;
    line-height: 1;
    letter-spacing: -4px;
  }
</style>
</head>
<body>
<main class="backdrop">
  <div class="flourish-row">
    <div class="flourish flourish--gold" role="img" aria-label="Gold scroll flourish"></div>
    <div class="flourish flourish--burgundy" role="img" aria-label="Burgundy scroll flourish"></div>
    <div class="flourish flourish--gold" role="img" aria-label="Gold scroll flourish"></div>
    <div class="flourish flourish--burgundy" role="img" aria-label="Burgundy scroll flourish"></div>
    <div class="flourish flourish--gold" role="img" aria-label="Gold scroll flourish"></div>
    <div class="flourish flourish--burgundy" role="img" aria-label="Burgundy scroll flourish"></div>
    <div class="flourish flourish--gold" role="img" aria-label="Gold scroll flourish"></div>
    <div class="flourish flourish--burgundy" role="img" aria-label="Burgundy scroll flourish"></div>
    <div class="flourish flourish--gold" role="img" aria-label="Gold scroll flourish"></div>
    <div class="flourish flourish--burgundy" role="img" aria-label="Burgundy scroll flourish"></div>
  </div>

  <section class="tile-grid">
    <div class="feature">
      <div class="feature__flourish" role="img" aria-label="White scroll flourish above monogram"></div>
      <div class="feature__monogram">H&amp;G</div>
      <div class="feature__flourish" role="img" aria-label="White scroll flourish below monogram"></div>
    </div>

    <!-- row 1 -->
    <div class="tile tile--burgundy"><div class="tile__flourish" role="img" aria-label="Scroll flourish"></div><div class="tile__monogram">H&amp;G</div><div class="tile__flourish" role="img" aria-label="Scroll flourish"></div></div>
    <div class="tile tile--gold"><div class="tile__flourish" role="img" aria-label="Scroll flourish"></div><div class="tile__monogram">H&amp;G</div><div class="tile__flourish" role="img" aria-label="Scroll flourish"></div></div>
    <div class="tile tile--burgundy"><div class="tile__flourish" role="img" aria-label="Scroll flourish"></div><div class="tile__monogram">H&amp;G</div><div class="tile__flourish" role="img" aria-label="Scroll flourish"></div></div>
    <div class="tile tile--gold"><div class="tile__flourish" role="img" aria-label="Scroll flourish"></div><div class="tile__monogram">H&amp;G</div><div class="tile__flourish" role="img" aria-label="Scroll flourish"></div></div>
    <div class="tile tile--burgundy"><div class="tile__flourish" role="img" aria-label="Scroll flourish"></div><div class="tile__monogram">H&amp;G</div><div class="tile__flourish" role="img" aria-label="Scroll flourish"></div></div>
    <div class="tile tile--gold"><div class="tile__flourish" role="img" aria-label="Scroll flourish"></div><div class="tile__monogram">H&amp;G</div><div class="tile__flourish" role="img" aria-label="Scroll flourish"></div></div>
    <div class="tile tile--burgundy"><div class="tile__flourish" role="img" aria-label="Scroll flourish"></div><div class="tile__monogram">H&amp;G</div><div class="tile__flourish" role="img" aria-label="Scroll flourish"></div></div>
    <div class="tile tile--gold"><div class="tile__flourish" role="img" aria-label="Scroll flourish"></div><div class="tile__monogram">H&amp;G</div><div class="tile__flourish" role="img" aria-label="Scroll flourish"></div></div>
    <div class="tile tile--burgundy"><div class="tile__flourish" role="img" aria-label="Scroll flourish"></div><div class="tile__monogram">H&amp;G</div><div class="tile__flourish" role="img" aria-label="Scroll flourish"></div></div>
    <div class="tile tile--gold"><div class="tile__flourish" role="img" aria-label="Scroll flourish"></div><div class="tile__monogram">H&amp;G</div><div class="tile__flourish" role="img" aria-label="Scroll flourish"></div></div>

    <!-- row 2 -->
    <div class="tile tile--gold"><div class="tile__flourish" role="img" aria-label="Scroll flourish"></div><div class="tile__monogram">H&amp;G</div><div class="tile__flourish" role="img" aria-label="Scroll flourish"></div></div>
    <div class="tile tile--burgundy"><div class="tile__flourish" role="img" aria-label="Scroll flourish"></div><div class="tile__monogram">H&amp;G</div><div class="tile__flourish" role="img" aria-label="Scroll flourish"></div></div>
    <div class="tile tile--gold"><div class="tile__flourish" role="img" aria-label="Scroll flourish"></div><div class="tile__monogram">H&amp;G</div><div class="tile__flourish" role="img" aria-label="Scroll flourish"></div></div>
    <div class="tile tile--burgundy"><div class="tile__flourish" role="img" aria-label="Scroll flourish"></div><div class="tile__monogram">H&amp;G</div><div class="tile__flourish" role="img" aria-label="Scroll flourish"></div></div>
    <div class="tile tile--gold"><div class="tile__flourish" role="img" aria-label="Scroll flourish"></div><div class="tile__monogram">H&amp;G</div><div class="tile__flourish" role="img" aria-label="Scroll flourish"></div></div>
    <div class="tile tile--burgundy"><div class="tile__flourish" role="img" aria-label="Scroll flourish"></div><div class="tile__monogram">H&amp;G</div><div class="tile__flourish" role="img" aria-label="Scroll flourish"></div></div>
    <div class="tile tile--gold"><div class="tile__flourish" role="img" aria-label="Scroll flourish"></div><div class="tile__monogram">H&amp;G</div><div class="tile__flourish" role="img" aria-label="Scroll flourish"></div></div>
    <div class="tile tile--burgundy"><div class="tile__flourish" role="img" aria-label="Scroll flourish"></div><div class="tile__monogram">H&amp;G</div><div class="tile__flourish" role="img" aria-label="Scroll flourish"></div></div>
    <div class="tile tile--gold"><div class="tile__flourish" role="img" aria-label="Scroll flourish"></div><div class="tile__monogram">H&amp;G</div><div class="tile__flourish" role="img" aria-label="Scroll flourish"></div></div>
    <div class="tile tile--burgundy"><div class="tile__flourish" role="img" aria-label="Scroll flourish"></div><div class="tile__monogram">H&amp;G</div><div class="tile__flourish" role="img" aria-label="Scroll flourish"></div></div>

    <!-- row 3 -->
    <div class="tile tile--burgundy"><div class="tile__flourish" role="img" aria-label="Scroll flourish"></div><div class="tile__monogram">H&amp;G</div><div class="tile__flourish" role="img" aria-label="Scroll flourish"></div></div>
    <div class="tile tile--gold"><div class="tile__flourish" role="img" aria-label="Scroll flourish"></div><div class="tile__monogram">H&amp;G</div><div class="tile__flourish" role="img" aria-label="Scroll flourish"></div></div>
    <div class="tile tile--burgundy"><div class="tile__flourish" role="img" aria-label="Scroll flourish"></div><div class="tile__monogram">H&amp;G</div><div class="tile__flourish" role="img" aria-label="Scroll flourish"></div></div>
    <div class="tile tile--gold"><div class="tile__flourish" role="img" aria-label="Scroll flourish"></div><div class="tile__monogram">H&amp;G</div><div class="tile__flourish" role="img" aria-label="Scroll flourish"></div></div>
    <div class="tile tile--burgundy"><div class="tile__flourish" role="img" aria-label="Scroll flourish"></div><div class="tile__monogram">H&amp;G</div><div class="tile__flourish" role="img" aria-label="Scroll flourish"></div></div>
    <div class="tile tile--gold"><div class="tile__flourish" role="img" aria-label="Scroll flourish"></div><div class="tile__monogram">H&amp;G</div><div class="tile__flourish" role="img" aria-label="Scroll flourish"></div></div>
    <div class="tile tile--burgundy"><div class="tile__flourish" role="img" aria-label="Scroll flourish"></div><div class="tile__monogram">H&amp;G</div><div class="tile__flourish" role="img" aria-label="Scroll flourish"></div></div>
    <div class="tile tile--gold"><div class="tile__flourish" role="img" aria-label="Scroll flourish"></div><div class="tile__monogram">H&amp;G</div><div class="tile__flourish" role="img" aria-label="Scroll flourish"></div></div>
    <div class="tile tile--burgundy"><div class="tile__flourish" role="img" aria-label="Scroll flourish"></div><div class="tile__monogram">H&amp;G</div><div class="tile__flourish" role="img" aria-label="Scroll flourish"></div></div>
    <div class="tile tile--gold"><div class="tile__flourish" role="img" aria-label="Scroll flourish"></div><div class="tile__monogram">H&amp;G</div><div class="tile__flourish" role="img" aria-label="Scroll flourish"></div></div>

    <!-- row 4 (sides of feature) -->
    <div class="tile tile--gold"><div class="tile__flourish" role="img" aria-label="Scroll flourish"></div><div class="tile__monogram">H&amp;G</div><div class="tile__flourish" role="img" aria-label="Scroll flourish"></div></div>
    <div class="tile tile--burgundy"><div class="tile__flourish" role="img" aria-label="Scroll flourish"></div><div class="tile__monogram">H&amp;G</div><div class="tile__flourish" role="img" aria-label="Scroll flourish"></div></div>
    <div class="tile tile--gold"><div class="tile__flourish" role="img" aria-label="Scroll flourish"></div><div class="tile__monogram">H&amp;G</div><div class="tile__flourish" role="img" aria-label="Scroll flourish"></div></div>
    <div class="tile tile--burgundy"><div class="tile__flourish" role="img" aria-label="Scroll flourish"></div><div class="tile__monogram">H&amp;G</div><div class="tile__flourish" role="img" aria-label="Scroll flourish"></div></div>
    <div class="tile tile--gold"><div class="tile__flourish" role="img" aria-label="Scroll flourish"></div><div class="tile__monogram">H&amp;G</div><div class="tile__flourish" role="img" aria-label="Scroll flourish"></div></div>
    <div class="tile tile--burgundy"><div class="tile__flourish" role="img" aria-label="Scroll flourish"></div><div class="tile__monogram">H&amp;G</div><div class="tile__flourish" role="img" aria-label="Scroll flourish"></div></div>

    <!-- row 5 (sides of feature) -->
    <div class="tile tile--burgundy"><div class="tile__flourish" role="img" aria-label="Scroll flourish"></div><div class="tile__monogram">H&amp;G</div><div class="tile__flourish" role="img" aria-label="Scroll flourish"></div></div>
    <div class="tile tile--gold"><div class="tile__flourish" role="img" aria-label="Scroll flourish"></div><div class="tile__monogram">H&amp;G</div><div class="tile__flourish" role="img" aria-label="Scroll flourish"></div></div>
    <div class="tile tile--burgundy"><div class="tile__flourish" role="img" aria-label="Scroll flourish"></div><div class="tile__monogram">H&amp;G</div><div class="tile__flourish" role="img" aria-label="Scroll flourish"></div></div>
    <div class="tile tile--gold"><div class="tile__flourish" role="img" aria-label="Scroll flourish"></div><div class="tile__monogram">H&amp;G</div><div class="tile__flourish" role="img" aria-label="Scroll flourish"></div></div>
    <div class="tile tile--burgundy"><div class="tile__flourish" role="img" aria-label="Scroll flourish"></div><div class="tile__monogram">H&amp;G</div><div class="tile__flourish" role="img" aria-label="Scroll flourish"></div></div>
    <div class="tile tile--gold"><div class="tile__flourish" role="img" aria-label="Scroll flourish"></div><div class="tile__monogram">H&amp;G</div><div class="tile__flourish" role="img" aria-label="Scroll flourish"></div></div>

    <!-- row 6 (sides of feature) -->
    <div class="tile tile--gold"><div class="tile__flourish" role="img" aria-label="Scroll flourish"></div><div class="tile__monogram">H&amp;G</div><div class="tile__flourish" role="img" aria-label="Scroll flourish"></div></div>
    <div class="tile tile--burgundy"><div class="tile__flourish" role="img" aria-label="Scroll flourish"></div><div class="tile__monogram">H&amp;G</div><div class="tile__flourish" role="img" aria-label="Scroll flourish"></div></div>
    <div class="tile tile--gold"><div class="tile__flourish" role="img" aria-label="Scroll flourish"></div><div class="tile__monogram">H&amp;G</div><div class="tile__flourish" role="img" aria-label="Scroll flourish"></div></div>
    <div class="tile tile--burgundy"><div class="tile__flourish" role="img" aria-label="Scroll flourish"></div><div class="tile__monogram">H&amp;G</div><div class="tile__flourish" role="img" aria-label="Scroll flourish"></div></div>
    <div class="tile tile--gold"><div class="tile__flourish" role="img" aria-label="Scroll flourish"></div><div class="tile__monogram">H&amp;G</div><div class="tile__flourish" role="img" aria-label="Scroll flourish"></div></div>
    <div class="tile tile--burgundy"><div class="tile__flourish" role="img" aria-label="Scroll flourish"></div><div class="tile__monogram">H&amp;G</div><div class="tile__flourish" role="img" aria-label="Scroll flourish"></div></div>

    <!-- row 7 -->
    <div class="tile tile--burgundy"><div class="tile__flourish" role="img" aria-label="Scroll flourish"></div><div class="tile__monogram">H&amp;G</div><div class="tile__flourish" role="img" aria-label="Scroll flourish"></div></div>
    <div class="tile tile--gold"><div class="tile__flourish" role="img" aria-label="Scroll flourish"></div><div class="tile__monogram">H&amp;G</div><div class="tile__flourish" role="img" aria-label="Scroll flourish"></div></div>
    <div class="tile tile--burgundy"><div class="tile__flourish" role="img" aria-label="Scroll flourish"></div><div class="tile__monogram">H&amp;G</div><div class="tile__flourish" role="img" aria-label="Scroll flourish"></div></div>
    <div class="tile tile--gold"><div class="tile__flourish" role="img" aria-label="Scroll flourish"></div><div class="tile__monogram">H&amp;G</div><div class="tile__flourish" role="img" aria-label="Scroll flourish"></div></div>
    <div class="tile tile--burgundy"><div class="tile__flourish" role="img" aria-label="Scroll flourish"></div><div class="tile__monogram">H&amp;G</div><div class="tile__flourish" role="img" aria-label="Scroll flourish"></div></div>
    <div class="tile tile--gold"><div class="tile__flourish" role="img" aria-label="Scroll flourish"></div><div class="tile__monogram">H&amp;G</div><div class="tile__flourish" role="img" aria-label="Scroll flourish"></div></div>
    <div class="tile tile--burgundy"><div class="tile__flourish" role="img" aria-label="Scroll flourish"></div><div class="tile__monogram">H&amp;G</div><div class="tile__flourish" role="img" aria-label="Scroll flourish"></div></div>
    <div class="tile tile--gold"><div class="tile__flourish" role="img" aria-label="Scroll flourish"></div><div class="tile__monogram">H&amp;G</div><div class="tile__flourish" role="img" aria-label="Scroll flourish"></div></div>
    <div class="tile tile--burgundy"><div class="tile__flourish" role="img" aria-label="Scroll flourish"></div><div class="tile__monogram">H&amp;G</div><div class="tile__flourish" role="img" aria-label="Scroll flourish"></div></div>
    <div class="tile tile--gold"><div class="tile__flourish" role="img" aria-label="Scroll flourish"></div><div class="tile__monogram">H&amp;G</div><div class="tile__flourish" role="img" aria-label="Scroll flourish"></div></div>

    <!-- row 8 -->
    <div class="tile tile--gold"><div class="tile__flourish" role="img" aria-label="Scroll flourish"></div><div class="tile__monogram">H&amp;G</div><div class="tile__flourish" role="img" aria-label="Scroll flourish"></div></div>
    <div class="tile tile--burgundy"><div class="tile__flourish" role="img" aria-label="Scroll flourish"></div><div class="tile__monogram">H&amp;G</div><div class="tile__flourish" role="img" aria-label="Scroll flourish"></div></div>
    <div class="tile tile--gold"><div class="tile__flourish" role="img" aria-label="Scroll flourish"></div><div class="tile__monogram">H&amp;G</div><div class="tile__flourish" role="img" aria-label="Scroll flourish"></div></div>
    <div class="tile tile--burgundy"><div class="tile__flourish" role="img" aria-label="Scroll flourish"></div><div class="tile__monogram">H&amp;G</div><div class="tile__flourish" role="img" aria-label="Scroll flourish"></div></div>
    <div class="tile tile--gold"><div class="tile__flourish" role="img" aria-label="Scroll flourish"></div><div class="tile__monogram">H&amp;G</div><div class="tile__flourish" role="img" aria-label="Scroll flourish"></div></div>
    <div class="tile tile--burgundy"><div class="tile__flourish" role="img" aria-label="Scroll flourish"></div><div class="tile__monogram">H&amp;G</div><div class="tile__flourish" role="img" aria-label="Scroll flourish"></div></div>
    <div class="tile tile--gold"><div class="tile__flourish" role="img" aria-label="Scroll flourish"></div><div class="tile__monogram">H&amp;G</div><div class="tile__flourish" role="img" aria-label="Scroll flourish"></div></div>
    <div class="tile tile--burgundy"><div class="tile__flourish" role="img" aria-label="Scroll flourish"></div><div class="tile__monogram">H&amp;G</div><div class="tile__flourish" role="img" aria-label="Scroll flourish"></div></div>
    <div class="tile tile--gold"><div class="tile__flourish" role="img" aria-label="Scroll flourish"></div><div class="tile__monogram">H&amp;G</div><div class="tile__flourish" role="img" aria-label="Scroll flourish"></div></div>
    <div class="tile tile--burgundy"><div class="tile__flourish" role="img" aria-label="Scroll flourish"></div><div class="tile__monogram">H&amp;G</div><div class="tile__flourish" role="img" aria-label="Scroll flourish"></div></div>
  </section>

  <div class="flourish-row">
    <div class="flourish flourish--burgundy" role="img" aria-label="Burgundy scroll flourish"></div>
    <div class="flourish flourish--gold" role="img" aria-label="Gold scroll flourish"></div>
    <div class="flourish flourish--burgundy" role="img" aria-label="Burgundy scroll flourish"></div>
    <div class="flourish flourish--gold" role="img" aria-label="Gold scroll flourish"></div>
    <div class="flourish flourish--burgundy" role="img" aria-label="Burgundy scroll flourish"></div>
    <div class="flourish flourish--gold" role="img" aria-label="Gold scroll flourish"></div>
    <div class="flourish flourish--burgundy" role="img" aria-label="Burgundy scroll flourish"></div>
    <div class="flourish flourish--gold" role="img" aria-label="Gold scroll flourish"></div>
    <div class="flourish flourish--burgundy" role="img" aria-label="Burgundy scroll flourish"></div>
    <div class="flourish flourish--gold" role="img" aria-label="Gold scroll flourish"></div>
  </div>
</main>
</body>
</html>
```